Brell Stone Company Business Cards

Front and Back Business Card - logo and text setup - cool design. I need workable photoshop or illustrator files so I can setup each employee card with design that is created
Updates

Hi everyone, thank you for the great entries. Please no more white and blue cards - there are so many already - black and silver only now please. thanks!

Target Market(s)

Construction Industry - Facility Managers

Industry/Entity Type

Construction

Contact Information for Business Card

I really like contemporary simplistic looks - clean neat....not opposed to seeing some black backrounds

Requirements
Must have
• Logo/website address with design on front only - www.brellstone-example.com (logo attached)
• Back:
• Name/Title/Company Address/Phone/email address
Nice to have
• Cool design
Should not have
• Nothing gimmicky like Fire or Water - since we are a Fire Protection company - it has all been done

```html
<!DOCTYPE html>
<html lang="en">
<head>
<meta charset="utf-8">
<title>Brell Stone Company – Business Cards</title>
<link rel="stylesheet" href="https://fonts.googleapis.com/css2?family=Open+Sans:wght@400;600;700;800&display=swap">
<style>
  :root {
    --page-bg: #2a2a2b;
    --card-bg: #141414;
    --card-edge: #262626;
    --brand-red: #ff2b20;
    --text-light: #f2f2f2;
    --text-soft: #d9d9d9;
    --divider: #6a6a6a;
  }
  * { box-sizing: border-box; margin: 0; padding: 0; }
  html, body {
    width: 1200px;
    height: 960px;
    overflow: hidden;
    background: var(--page-bg);
    font-family: "Open Sans", Arial, sans-serif;
  }
  .sheet {
    position: relative;
    width: 1200px;
    height: 960px;
  }
  .card {
    position: absolute;
    left: 220px;
    width: 760px;
    height: 434px;
    background: var(--card-bg);
    border: 1px solid var(--card-edge);
    border-radius: 6px;
    box-shadow: 0 18px 40px rgba(0, 0, 0, 0.45);
  }
  .card--front { top: 30px; }
  .card--back { top: 496px; }

  .brand-name {
    font-family: "Open Sans", Arial, sans-serif;
    font-weight: 800;
    color: var(--brand-red);
    letter-spacing: -1px;
    line-height: 1;
    white-space: nowrap;
  }

  /* Front */
  .card--front .brand-name {
    position: absolute;
    top: 130px;
    left: 0;
    width: 100%;
    text-align: center;
    font-size: 78px;
  }
  .front-web {
    position: absolute;
    top: 278px;
    left: 0;
    width: 100%;
    text-align: center;
    font-size: 22px;
    letter-spacing: 5px;
    color: var(--text-soft);
  }

  /* Back */
  .card--back .brand-name {
    position: absolute;
    top: 178px;
    left: 48px;
    font-size: 52px;
  }
  .back-divider {
    position: absolute;
    left: 396px;
    top: 92px;
    width: 1px;
    height: 250px;
    background: var(--divider);
  }
  .contact {
    position: absolute;
    left: 426px;
    top: 96px;
    color: var(--text-light);
  }
  .contact-name {
    font-size: 22px;
    font-weight: 700;
    line-height: 1.2;
  }
  .contact-title {
    font-size: 18px;
    color: var(--text-soft);
    margin-bottom: 18px;
  }
  .contact-list { list-style: none; }
  .contact-list li {
    display: flex;
    align-items: center;
    gap: 10px;
    font-size: 17px;
    line-height: 1;
    margin-bottom: 12px;
  }
  .contact-list svg { width: 16px; height: 16px; flex: none; }
  .contact-address {
    margin-top: 14px;
    font-size: 17px;
    line-height: 1.4;
    font-style: normal;
    color: var(--text-soft);
  }
</style>
</head>
<body>
<main class="sheet">

  <section class="card card--front" aria-label="Card front">
    <p class="brand-name">Brell Stone</p>
    <p class="front-web">www.brellstone-example.com</p>
  </section>

  <section class="card card--back" aria-label="Card back">
    <p class="brand-name">Brell Stone</p>
    <div class="back-divider"></div>
    <div class="contact">
      <p class="contact-name">Dana Marlow</p>
      <p class="contact-title">President</p>
      <ul class="contact-list">
        <li>
          <svg viewBox="0 0 16 16" aria-hidden="true">
            <path d="M3.5 1.5 L6 1.5 L7 5 L5.4 6.2 C6.3 8 7.9 9.7 9.8 10.6 L11 9 L14.5 10 L14.5 12.5 C14.5 13.6 13.6 14.5 12.5 14.5 C6.7 14.5 1.5 9.3 1.5 3.5 C1.5 2.4 2.4 1.5 3.5 1.5 Z" fill="var(--brand-red)"/>
          </svg>
          (555) 014-2290
        </li>
        <li>
          <svg viewBox="0 0 16 16" aria-hidden="true">
            <rect x="1" y="3" width="14" height="10" fill="var(--brand-red)"/>
            <path d="M1.5 3.5 L8 9 L14.5 3.5" fill="none" stroke="var(--card-bg)" stroke-width="1.3"/>
          </svg>
          info@brellstone-example.com
        </li>
        <li>
          <svg viewBox="0 0 16 16" aria-hidden="true">
            <circle cx="8" cy="8" r="7" fill="var(--brand-red)"/>
            <g fill="none" stroke="var(--card-bg)" stroke-width="1">
              <ellipse cx="8" cy="8" rx="3" ry="6.5"/>
              <line x1="1" y1="8" x2="15" y2="8"/>
              <line x1="8" y1="1" x2="8" y2="15"/>
            </g>
          </svg>
          www.brellstone-example.com
        </li>
      </ul>
      <address class="contact-address">
        48 Harbor Lane<br>
        Millbrook, NY 10000
      </address>
    </div>
  </section>

</main>
</body>
</html>
```